AI Business Tools Landing Page

My web-based website builder (Pavlora.com) will be adding many new features in the very near future and I need an eye-catching landing page to promote these new products.

The page will have a primary section of the 8 main products we are promoting:
1. AI Instant Website Generator
2. AI Chatbot
3. Online Store Builder with AI Assistance
4. AI Auto-Blogging System
5. Online Scheduling System
6. Custom Email System
7. SEO Service
8. CRM System

The page will also have a smaller section for links to our affiliate programs. These can be smaller, less-promanent buttons or links. These are the affiliate products:
1. Get Your LLC
2. Website Design and Maintenance
3. Searchly Ads Management
4. Social Media Posting Service
5. Logo Design
6. Trademark Registration
7. Patent Application
8. Printing Services (including postcards, flyers, and merch.)
9. Bulk AI Content Generator

The theme and color scheme of the page should follow the theme of our main website, which is https://pavlora.com.

I need the page fully coded and ready to deploy on my server.

I look forward to seeing your amazing designs!

```html
<!DOCTYPE html>
<html lang="en">
<head>
<meta charset="utf-8">
<title>Pavlora – AI Business Tools</title>
<link href="https://fonts.googleapis.com/css2?family=Poppins:wght@300;400;500;600;700&family=Lora:wght@400&display=swap" rel="stylesheet">
<style>
:root{
  --blue:#1592e0;
  --blue-light:#23a8e8;
  --blue-deep:#0a6fcf;
  --navy:#0b1738;
  --navy-mid:#12306b;
  --ink:#1c2230;
  --muted:#50586a;
  --tile:#3fa8ea;
  --white:#ffffff;
  --card-border:#e4e8ee;
  --halo:#e7e9ef;
}
*{margin:0;padding:0;box-sizing:border-box}
html,body{width:1200px;height:2512px;overflow:hidden}
body{position:relative;background:var(--white);font-family:"Poppins",sans-serif;color:var(--ink)}
.abs{position:absolute}

/* header */
.site-header{left:0;top:0;width:1200px;height:72px;background:var(--white);border-bottom:1px solid #e8ebf0}
.brand{left:90px;top:18px;display:flex;align-items:center;gap:10px;font-size:24px;font-weight:600;color:#2b3445}
.brand-dot{width:30px;height:30px;border-radius:50%;background:var(--blue-light)}
.main-nav{left:365px;top:27px;display:flex;gap:25px;font-size:14px;color:#2b3445}
.btn{display:flex;align-items:center;justify-content:center;color:var(--white);background:linear-gradient(90deg,var(--blue-light),var(--blue));border-radius:0 10px 0 10px;font-family:"Poppins",sans-serif}
.header-cta{left:1005px;top:15px;width:143px;height:42px;font-size:14px}

/* hero */
.hero-art{left:0;top:72px}
.hero-title{left:143px;top:198px;font-size:41px;line-height:53px;font-weight:300;color:var(--white)}
.hero-title b{font-weight:700}
.hero-sub{left:143px;top:372px;width:400px;font-family:"Lora",serif;font-size:17px;line-height:25px;color:var(--white)}
.hero-cta{left:146px;top:447px;width:158px;height:46px;font-size:18px}

/* features */
.section-title{left:0;width:1200px;text-align:center;font-size:40px;font-weight:400}
.features-title{top:838px;color:var(--ink)}
.features-title span{color:var(--blue-light);font-weight:600}
.section-sub{left:0;top:897px;width:1200px;text-align:center;font-family:"Lora",serif;font-size:19px;color:var(--muted)}
.rule{height:3px;width:110px;left:545px;background:var(--blue)}
.feature-card{width:250px;height:252px;background:var(--white);border:2px solid var(--card-border);border-radius:4px;box-shadow:0 2px 6px rgba(0,0,0,.05)}
.feature-card.is-active{background:var(--blue);border-color:var(--blue);box-shadow:0 8px 20px rgba(21,146,224,.3)}
.card-icon{position:absolute;left:26px;top:26px;width:84px;height:64px}
.card-name{position:absolute;left:26px;top:108px;width:220px;font-size:17px;line-height:21px;font-weight:600;color:#222a3a}
.is-active .card-name{color:var(--white);top:94px}
.card-btn{position:absolute;left:66px;top:176px;width:118px;height:36px;font-size:13px}
.is-active .card-btn{background:var(--white);color:#333;top:160px}
.features-cta{left:493px;top:1588px;width:214px;height:46px;font-size:18px}

/* tools */
.tools-band{left:0;top:1698px}
.tools-title{top:1842px;color:var(--white);font-weight:300;line-height:52px}
.tools-title b{font-weight:600}
.tools-rule{top:1955px;background:var(--white)}
.tool-link{width:212px;height:80px;background:var(--tile);border-radius:8px;display:flex;align-items:center;justify-content:center;text-align:center;font-size:16px;line-height:21px;color:var(--white);font-weight:300}
.tools-cta{left:517px;top:2303px;width:166px;height:46px;font-size:18px;background:var(--white);color:var(--ink)}

/* footer */
.site-footer{left:0;top:2380px}
.copyright{left:0;top:2452px;width:1200px;text-align:center;font-size:15px;color:#8a93a8}
</style>
</head>
<body>

<header class="site-header abs">
  <div class="brand abs"><span class="brand-dot"></span>Pavlora</div>
  <nav class="main-nav abs"><span>About Us</span><span>Learn More</span><span>Make Money</span><span>History of AI</span><span>Pricing</span><span>Blog</span></nav>
  <a class="btn header-cta abs">Get Started</a>
</header>

<svg class="hero-art abs" width="1200" height="720" viewBox="0 0 1200 720" role="img" aria-label="Hero photograph: a person at a computer rendered as a glowing network of blue and orange points on a dark navy background">
  <defs>
    <radialGradient id="heroGlow" cx="72%" cy="40%" r="70%">
      <stop offset="0" stop-color="#1c4fa0"/>
      <stop offset=".5" stop-color="#13306e"/>
      <stop offset="1" stop-color="#0a1535"/>
    </radialGradient>
  </defs>
  <polygon points="0,450 0,0 1200,0 1200,460 1125,505 1110,550 410,713 120,545" fill="#1a9ae6"/>
  <polygon points="0,440 0,0 1200,0 1200,455 1115,500 1100,545 410,705 115,520" fill="url(#heroGlow)"/>
</svg>
<h1 class="hero-title abs">Create a website<br>with <b>Pavlora</b><br><b>AI Website Builder</b></h1>
<p class="hero-sub abs">Your FREE Stunning Website In 1-Click Built by Artificial Intelligence</p>
<a class="btn hero-cta abs">Get Started</a>

<h2 class="section-title features-title abs"><span>Additional Features</span> for your website</h2>
<p class="section-sub abs">Lorem Ipsum is simply dummy text of the printing and typesetting</p>
<div class="rule abs" style="top:942px"></div>

<section>
  <div class="feature-card abs" style="left:88px;top:985px">
    <svg class="card-icon" viewBox="0 0 84 64"><circle cx="56" cy="34" r="22" fill="var(--halo)"/><g fill="none" stroke="var(--blue)" stroke-width="2.5"><path d="M12 42a12 12 0 0 1 4-24 16 16 0 0 1 30-2 12 12 0 0 1 4 26z"/><circle cx="32" cy="30" r="6"/><path d="M32 20v4M32 36v4M22 30h4M38 30h4"/></g></svg>
    <div class="card-name">AI Instant Website Generator</div>
    <a class="btn card-btn">Learn more</a>
  </div>
  <div class="feature-card is-active abs" style="left:347px;top:970px">
    <svg class="card-icon" viewBox="0 0 84 64"><circle cx="56" cy="30" r="22" fill="#1a7fc4"/><g fill="none" stroke="var(--white)" stroke-width="2.5"><rect x="4" y="6" width="48" height="40" rx="3"/><path d="M4 38h48M20 54h16M28 46v8M22 20l-5 6 5 6M34 20l5 6-5 6M30 18l-4 16"/></g></svg>
    <div class="card-name">AI Chatbot</div>
    <a class="btn card-btn">Learn More</a>
  </div>
  <div class="feature-card abs" style="left:605px;top:985px;height:260px">
    <svg class="card-icon" viewBox="0 0 84 64"><circle cx="56" cy="34" r="22" fill="var(--halo)"/><g fill="none" stroke="var(--blue)" stroke-width="2.5"><circle cx="36" cy="16" r="9"/><path d="M6 44l14-12 12 10 12-10 18 12-22 16z"/></g></svg>
    <div class="card-name">Online Store Builder with AI Assistance</div>
    <a class="btn card-btn" style="top:180px">Learn more</a>
  </div>
  <div class="feature-card abs" style="left:863px;top:985px;height:260px">
    <svg class="card-icon" viewBox="0 0 84 64"><circle cx="56" cy="34" r="22" fill="var(--halo)"/><g fill="none" stroke="var(--blue)" stroke-width="2.5"><path d="M8 4h38v56H8z"/><path d="M16 16h22M16 26h22M16 36h14M30 48l8 8 18-20"/></g></svg>
    <div class="card-name">AI Auto-Blogging System</div>
    <a class="btn card-btn" style="top:180px">Learn more</a>
  </div>

  <div class="feature-card abs" style="left:88px;top:1280px;height:260px">
    <svg class="card-icon" viewBox="0 0 84 64"><circle cx="56" cy="34" r="22" fill="var(--halo)"/><g fill="none" stroke="var(--blue)" stroke-width="2.5"><rect x="22" y="22" width="14" height="14"/><rect x="24" y="2" width="10" height="10"/><rect x="24" y="46" width="10" height="10"/><rect x="2" y="24" width="10" height="10"/><rect x="46" y="24" width="10" height="10"/><path d="M29 12v10M29 36v10M12 29h10M36 29h10"/></g></svg>
    <div class="card-name">Online Scheduling System</div>
    <a class="btn card-btn" style="top:180px">Learn more</a>
  </div>
  <div class="feature-card abs" style="left:347px;top:1280px;height:260px">
    <svg class="card-icon" viewBox="0 0 84 64"><circle cx="60" cy="34" r="22" fill="var(--halo)"/><g fill="none" stroke="var(--blue)" stroke-width="2.5"><rect x="2" y="4" width="56" height="44" rx="2"/><rect x="10" y="14" width="12" height="8"/><rect x="26" y="14" width="12" height="8"/><rect x="42" y="14" width="10" height="8"/><path d="M10 32h40M22 56h16M30 48v8"/></g></svg>
    <div class="card-name">Custom Email System</div>
    <a class="btn card-btn" style="top:180px">Learn more</a>
  </div>
  <div class="feature-card abs" style="left:605px;top:1280px;height:260px">
    <svg class="card-icon" viewBox="0 0 84 64"><circle cx="56" cy="34" r="22" fill="var(--halo)"/><g fill="none" stroke="var(--blue)" stroke-width="2.5"><circle cx="34" cy="24" r="20"/><circle cx="34" cy="24" r="14"/><path d="M18 40L4 56"/></g></svg>
    <div class="card-name">SEO Service</div>
    <a class="btn card-btn" style="top:180px">Learn more</a>
  </div>
  <div class="feature-card abs" style="left:863px;top:1280px;height:260px">
    <svg class="card-icon" viewBox="0 0 84 64"><circle cx="56" cy="34" r="22" fill="var(--halo)"/><g fill="none" stroke="var(--blue)" stroke-width="2.5"><circle cx="26" cy="24" r="18"/><circle cx="26" cy="24" r="7"/><rect x="4" y="42" width="46" height="16" rx="3"/></g></svg>
    <div class="card-name">CRM System</div>
    <a class="btn card-btn" style="top:180px">Learn more</a>
  </div>
</section>
<a class="btn features-cta abs">Additional Features</a>

<svg class="tools-band abs" width="1200" height="700" viewBox="0 0 1200 700" aria-hidden="true">
  <polygon points="0,257 0,700 1200,700 1200,242 1125,202 1110,150 410,0 120,152" fill="var(--blue-deep)"/>
  <polygon points="0,262 0,700 1200,700 1200,255 1128,215 1112,165 410,10 140,160" fill="var(--blue)"/>
</svg>
<h2 class="section-title tools-title abs">More tools to help <b>your grow<br>your business</b></h2>
<div class="rule tools-rule abs"></div>

<nav>
  <a class="tool-link abs" style="left:266px;top:1990px">Get Your LLC</a>
  <a class="tool-link abs" style="left:494px;top:1990px">Website Design<br>and Maintenance</a>
  <a class="tool-link abs" style="left:722px;top:1990px">Searchly Ads<br>Management</a>
  <a class="tool-link abs" style="left:266px;top:2087px">Social Media<br>Posting Service</a>
  <a class="tool-link abs" style="left:494px;top:2087px">Logo Design</a>
  <a class="tool-link abs" style="left:722px;top:2087px">Trademark<br>Registration</a>
  <a class="tool-link abs" style="left:266px;top:2184px">Patent Application</a>
  <a class="tool-link abs" style="left:494px;top:2184px">Printing Services</a>
  <a class="tool-link abs" style="left:722px;top:2184px">Bulk AI Content<br>Generator</a>
</nav>
<a class="btn tools-cta abs">More Tools</a>

<svg class="site-footer abs" width="1200" height="132" viewBox="0 0 1200 132" aria-hidden="true">
  <polygon points="0,14 1200,0 1200,132 0,132" fill="var(--navy)"/>
</svg>
<p class="copyright abs">Copyright © pavlora 2024. All rights reserved. | Privacy Policy</p>

</body>
</html>
```